Brell Stone Company Business Cards

Front and Back Business Card - logo and text setup - cool design. I need workable photoshop or illustrator files so I can setup each employee card with design that is created
Updates

Hi everyone, thank you for the great entries. Please no more white and blue cards - there are so many already - black and silver only now please. thanks!

Target Market(s)

Construction Industry - Facility Managers

Industry/Entity Type

Construction

Contact Information for Business Card

I really like contemporary simplistic looks - clean neat....not opposed to seeing some black backrounds

Requirements
Must have
• Logo/website address with design on front only - www.brellstone-example.com (logo attached)
• Back:
• Name/Title/Company Address/Phone/email address
Nice to have
• Cool design
Should not have
• Nothing gimmicky like Fire or Water - since we are a Fire Protection company - it has all been done

```html
<!DOCTYPE html>
<html lang="en">
<head>
<meta charset="utf-8">
<title>Brell Stone Company Business Cards</title>
<link href="https://fonts.googleapis.com/css2?family=Open+Sans:ital,wght@0,400;0,600;0,800;1,700&display=swap" rel="stylesheet">
<style>
  :root {
    --page-bg: #1c1c1e;
    --card-black: #050505;
    --silver: #8a8a8a;
    --silver-light: #c9c9c9;
    --royal-blue: #0a23a0;
    --fire-red: #ff2222;
    --coral: #ff5a4e;
    --white: #ffffff;
  }
  * { box-sizing: border-box; margin: 0; padding: 0; }
  html, body {
    width: 1200px; height: 960px; overflow: hidden;
    background: var(--page-bg);
    font-family: "Open Sans", Arial, sans-serif;
  }
  .sheet {
    position: relative; width: 1200px; height: 960px;
    display: flex; flex-direction: column; align-items: center; justify-content: center; gap: 60px;
  }
  .card {
    position: relative; width: 700px; height: 400px;
    background: var(--card-black); overflow: hidden;
    box-shadow: 0 18px 40px rgba(0,0,0,.55);
  }
  /* Front */
  .card-front { display: flex; flex-direction: column; align-items: center; justify-content: center; }
  .front-wordmark {
    font-weight: 800; font-size: 84px; letter-spacing: -2px; line-height: 1;
    color: var(--silver);
  }
  .front-web {
    margin-top: 44px; font-size: 17px; letter-spacing: 4px; color: var(--silver-light);
  }
  /* Back */
  .back-art { position: absolute; inset: 0; width: 700px; height: 400px; }
  .back-wordmark {
    position: absolute; left: 40px; top: 70px;
    font-weight: 800; font-size: 60px; letter-spacing: -1.5px; line-height: 1;
    color: var(--royal-blue);
  }
  .contact {
    position: absolute; right: 36px; top: 120px; text-align: right; color: var(--white);
  }
  .contact-name { font-weight: 700; font-style: italic; font-size: 22px; line-height: 1.1; }
  .contact-title { font-weight: 700; font-style: italic; font-size: 18px; margin-bottom: 16px; }
  .contact-line {
    display: flex; justify-content: flex-end; align-items: center; gap: 10px;
    font-size: 16px; line-height: 1.7;
  }
  .contact-line svg { width: 15px; height: 15px; fill: var(--white); flex: none; }
  .contact-address { margin-top: 10px; font-size: 16px; line-height: 1.4; padding-right: 25px; }
</style>
</head>
<body>
<main class="sheet">
  <section class="card card-front" aria-label="Business card front">
    <div class="front-wordmark">Brell Stone</div>
    <div class="front-web">www.brellstone-example.com</div>
  </section>

  <section class="card card-back" aria-label="Business card back">
    <svg class="back-art" viewBox="0 0 700 400" aria-hidden="true">
      <path d="M400,0 C480,120 380,220 260,300 C200,340 160,370 140,400 L700,400 L700,0 Z" fill="var(--coral)"/>
      <path d="M425,0 C505,120 405,225 290,305 C235,342 200,372 185,400 L700,400 L700,0 Z" fill="var(--fire-red)"/>
      <path d="M470,0 C550,120 450,230 340,310 C290,345 260,375 250,400 L700,400 L700,0 Z" fill="var(--royal-blue)"/>
    </svg>
    <div class="back-wordmark">Brell Stone</div>
    <div class="contact">
      <div class="contact-name">Dana Whitfield</div>
      <div class="contact-title">President</div>
      <div class="contact-line">(555) 014-2270
        <svg viewBox="0 0 24 24"><path d="M6.6 10.8a15 15 0 0 0 6.6 6.6l2.2-2.2c.3-.3.7-.4 1-.2 1.1.4 2.3.6 3.6.6.6 0 1 .4 1 1V20c0 .6-.4 1-1 1A17 17 0 0 1 3 4c0-.6.4-1 1-1h3.5c.6 0 1 .4 1 1 0 1.3.2 2.5.6 3.6.1.3 0 .7-.2 1z"/></svg>
      </div>
      <div class="contact-line">info@brellstone-example.com
        <svg viewBox="0 0 24 24"><path d="M2 5h20v14H2z M3.5 6.5 12 13l8.5-6.5" fill="none" stroke="#fff" stroke-width="2"/></svg>
      </div>
      <div class="contact-line">www.brellstone-example.com
        <svg viewBox="0 0 24 24"><g fill="none" stroke="#fff" stroke-width="2"><circle cx="12" cy="12" r="9.5"/><ellipse cx="12" cy="12" rx="4" ry="9.5"/><path d="M2.5 12h19M4 7h16M4 17h16"/></g></svg>
      </div>
      <div class="contact-address">48 Quarry Lane<br>Millbrook Falls, NY 10000</div>
    </div>
  </section>
</main>
</body>
</html>
```